kolvarin.link kolvarin.space kolvarin.press website

The website is named KOLVARIN and it will have 3 domain names. kolvarin.link, press, space.
I'd like it to be viewed on Pads, pcs and phones.

page menu:

kolvarin.link(start page): presentation of company. (creative, design, app, new product innovation.)
Here we'll need sosial media icons: plimber, vendoloop, mirtavel, trelvanet. (light but some 'fruity' colors)

kolvarin.press: blog. It will be a 75% picture blog > rest will be text. I need to be able to resize pictures and shape columns to picture size. (light but some 'fruity' colors)

kolvarin.space : the fun part of this web design, however, on entering the page I'd like a non-disclosure agreement where viewer simply click "yes, I agree" after filling out contact info. (check attached document)
We will have space here for uploading PDF files viewers can download. There is also a blog space here to tell in brief about the PDF file. (maybe a space/sci-fi theme her e.g spacechimp, Laika the space dog?)

I will attach the logo here I want you to use > and develop for the .space .press webpage. The logo i uploaded is for the .link page.

Target Market(s)

venture capitalists

Number of Pages Required

3 page

Requirements
Must have
• a few 'fruity colors' but mostly white and grey

```html
<!DOCTYPE html>
<html lang="en">
<head>
<meta charset="utf-8">
<title>Kolvarin — Creative design, app creation, new product innovation</title>
<link rel="stylesheet" href="https://fonts.googleapis.com/css2?family=Orbitron:wght@600;700&family=Open+Sans:ital,wght@0,400;0,600;0,700;1,400;1,600&display=swap">
<style>
:root{
  --green:#4fa846;
  --green-dark:#3f9437;
  --red:#e5452f;
  --orange:#f39a1e;
  --purple:#8e3fa8;
  --blue:#2d8fd5;
  --ink:#2a2a2a;
  --text:#6f6f6f;
  --muted:#8a8a8a;
  --line:#dcdcdc;
  --footer:#262626;
  --footer-text:#cfcfcf;
  --white:#ffffff;
  --display:"Orbitron", sans-serif;
  --body:"Open Sans", sans-serif;
}
*{box-sizing:border-box;margin:0;padding:0}
html,body{width:1200px;height:2375px;overflow:hidden}
body{font-family:var(--body);color:var(--text);background:var(--white);position:relative}
a{text-decoration:none;color:inherit}
ul{list-style:none}

.rainbow{height:4px;background:linear-gradient(90deg,var(--purple) 0%,var(--blue) 25%,var(--green) 50%,var(--orange) 75%,var(--red) 100%)}

/* header */
.site-header{position:absolute;top:0;left:0;width:1200px;height:71px;background:var(--white);z-index:5}
.brand{position:absolute;left:98px;top:20px;display:flex;align-items:center;gap:10px}
.brand-mark{width:16px;height:16px;background:var(--green);border-radius:50%;flex:none}
.brand-name{font-family:var(--display);font-weight:700;font-size:22px;color:var(--ink);letter-spacing:1px;white-space:nowrap}
.main-nav{position:absolute;right:245px;top:28px;display:flex;gap:18px;align-items:center}
.main-nav a{font-family:var(--display);font-weight:600;font-size:11px;color:var(--ink);letter-spacing:.6px;text-transform:uppercase;white-space:nowrap}
.main-nav a.is-active{color:var(--green)}
.header-tools{position:absolute;left:975px;top:17px;display:flex;gap:10px;align-items:center}
.search-btn{width:22px;height:22px;display:flex;align-items:center;justify-content:center}
.round-btn{width:38px;height:38px;border-radius:50%;display:flex;align-items:center;justify-content:center}
.round-btn.lock{background:var(--red)}
.round-btn.edit{background:var(--green)}

/* hero */
.hero{position:absolute;top:71px;left:0;width:1200px;height:449px;overflow:hidden}
.hero-visual{position:absolute;inset:0;background:radial-gradient(circle at 78% 32%,#f7e6a0 0%,#b38a3b 8%,#3a3d48 28%,#15181f 60%,#0b0c10 100%)}
.hero-visual::after{content:"";position:absolute;inset:0;background:radial-gradient(ellipse at 55% 25%,rgba(120,90,200,.35) 0%,rgba(0,0,0,0) 45%)}
.hero-panel{position:absolute;left:100px;top:120px;width:440px;height:250px;background:rgba(0,0,0,.45);padding:36px 20px 36px 31px}
.hero-title{font-family:var(--display);font-weight:700;font-size:32px;color:var(--white);letter-spacing:2px;line-height:1}
.hero-lead{margin-top:14px;font-style:italic;font-weight:600;font-size:18px;line-height:29px;color:var(--white);white-space:nowrap}
.btn{display:inline-block;background:var(--green);color:var(--white);font-family:var(--body);font-weight:700;font-size:14px;text-transform:uppercase;border:2px solid var(--white);padding:10px 24px;letter-spacing:.3px}
.hero .btn{margin-top:22px}
.slider-dots{display:flex;gap:5px;justify-content:center}
.slider-dots span{width:14px;height:14px;border-radius:50%;border:2px solid var(--white)}
.slider-dots span.is-on{background:var(--red);border-color:var(--white)}
.hero .slider-dots{position:absolute;left:0;right:0;top:397px}

/* section titles */
.section-title{font-family:var(--display);font-weight:700;font-size:25px;color:var(--ink);letter-spacing:2px;text-transform:uppercase;text-align:center;white-space:nowrap}

/* welcome */
.welcome{position:absolute;top:520px;left:0;width:1200px;height:470px}
.welcome .section-title{margin-top:42px}
.welcome-intro{width:820px;margin:22px auto 0;text-align:center;font-size:12px;line-height:23px;color:var(--muted)}
.services{position:absolute;top:158px;left:0;width:1200px}
.service{position:absolute;width:300px;text-align:center}
.service:nth-child(1){left:87px}
.service:nth-child(2){left:450px}
.service:nth-child(3){left:811px}
.service-icon{width:150px;height:150px;margin:0 auto;border-radius:50%;display:flex;align-items:center;justify-content:center;border:2px solid}
.service-icon .disc{width:136px;height:136px;border-radius:50%;display:flex;align-items:center;justify-content:center}
.service--design .service-icon{border-color:var(--red)} .service--design .disc{background:var(--red)}
.service--app .service-icon{border-color:var(--green)} .service--app .disc{background:var(--green)}
.service--idea .service-icon{border-color:var(--orange)} .service--idea .disc{background:var(--orange)}
.service h3{margin-top:20px;font-family:var(--display);font-weight:600;font-size:13px;color:var(--ink);letter-spacing:1.2px;text-transform:uppercase;white-space:nowrap}
.service p{margin-top:10px;font-size:12px;line-height:23px;color:var(--muted)}
.read-more{display:inline-block;margin-top:12px;font-size:12px;font-weight:700;color:var(--red);text-transform:uppercase}

/* get started band */
.cta-band{position:absolute;top:990px;left:0;width:1200px;height:232px;overflow:hidden;text-align:center}
.cta-visual{position:absolute;inset:0;background:linear-gradient(180deg,#3b4a55 0%,#2c3842 55%,#1f262d 100%)}
.cta-content{position:relative;padding-top:36px}
.cta-content .section-title{color:var(--white);font-size:29px}
.cta-content p{width:700px;margin:14px auto 0;font-style:italic;font-weight:600;font-size:15px;line-height:26px;color:var(--white)}
.cta-content .btn{margin-top:16px;padding:9px 24px}

/* key features */
.features{position:absolute;top:1222px;left:0;width:1200px;height:368px}
.devices-visual{position:absolute;left:98px;top:46px;width:478px;height:274px;background:linear-gradient(135deg,#f1efe9 0%,#e0ddd4 50%,#f2f1ee 100%);border-radius:6px}
.features-copy{position:absolute;left:650px;top:42px;width:480px}
.features-copy .section-title{text-align:left;font-size:24px}
.feature-list{margin-top:24px}
.feature-list li{display:flex;align-items:center;gap:11px;font-size:12px;color:var(--text);height:37px;white-space:nowrap}
.tick{width:12px;height:12px;flex:none}
.features-copy .read-more{color:var(--green);margin-top:14px}

/* testimonials */
.testimonials{position:absolute;top:1590px;left:0;width:1200px;height:250px;overflow:hidden}
.testimonials-visual{position:absolute;inset:0;background:linear-gradient(180deg,#5cb552 0%,#4fa846 100%)}
.testimonials .section-title{position:relative;margin-top:34px;color:var(--white);font-size:25px}
.quote-badge{position:absolute;left:105px;top:86px;width:112px;height:112px;border-radius:50%;background:#e7e7e7;display:flex;align-items:center;padding-left:18px}
.avatar{position:absolute;left:175px;top:86px;width:112px;height:112px;border-radius:50%;background:linear-gradient(160deg,#c9c9c9,#8b8b8b);border:4px solid var(--white)}
.testimonial-text{position:absolute;left:320px;top:90px;width:790px;font-style:italic;font-size:12px;line-height:23px;color:var(--white)}
.testimonial-name{position:absolute;left:320px;top:170px;font-weight:700;font-size:14px;color:var(--white);text-transform:uppercase}
.testimonials .slider-dots{position:absolute;left:0;right:0;top:218px}
.testimonials .slider-dots span.is-on{background:var(--white)}

/* partners */
.partners{position:absolute;top:1840px;left:0;width:1200px;height:220px}
.partners .section-title{margin-top:40px;font-size:24px}
.partner-row{position:absolute;top:95px;left:183px;display:flex;gap:15px}
.partner{width:155px;height:76px;border:1px solid var(--line);display:flex;align-items:center;justify-content:center}
.partner-badge{width:90px;height:30px;border-radius:4px}
.carousel-arrow{position:absolute;top:118px;width:16px;height:28px}
.carousel-arrow.prev{left:100px}
.carousel-arrow.next{left:1086px}

/* footer */
.site-footer{position:absolute;top:2060px;left:0;width:1200px;height:315px;background:var(--footer)}
.footer-brand{position:absolute;left:75px;top:60px;display:flex;align-items:center;gap:9px}
.footer-brand .brand-name{color:var(--white);font-size:22px}
.footer-cols{position:absolute;left:295px;top:24px;display:flex;height:210px}
.footer-col{border-left:1px solid #3a3a3a;padding-left:25px;height:210px}
.footer-col:nth-child(1){width:140px}
.footer-col:nth-child(2){width:163px}
.footer-col:nth-child(3){width:193px}
.footer-col:nth-child(4){width:162px}
.footer-col:nth-child(5){width:160px}
.footer-col h4{font-family:var(--display);font-weight:600;font-size:12px;color:var(--white);letter-spacing:1.2px;text-transform:uppercase;margin-top:8px;white-space:nowrap}
.footer-col ul{margin-top:14px}
.footer-col li{font-size:12px;line-height:23px;color:var(--footer-text);white-space:nowrap}
.copyright{position:absolute;left:100px;top:271px;font-size:12px;color:var(--footer-text)}
.social{position:absolute;right:40px;top:263px;display:flex;gap:6px}
.social a{height:30px;padding:0 7px;border-radius:4px;display:flex;align-items:center;font-size:10px;font-weight:600;color:var(--white);white-space:nowrap}
.social .mirtavel{background:var(--blue)}
.social .plimber{background:var(--orange)}
.social .trelvanet{background:var(--red)}
.social .vendoloop{background:var(--purple)}
</style>
</head>
<body>

<header class="site-header">
  <div class="rainbow"></div>
  <a class="brand" href="#">
    <span class="brand-mark"></span>
    <span class="brand-name">KOLVARIN</span>
  </a>
  <nav class="main-nav">
    <a class="is-active" href="#">Home</a>
    <a href="#">About us</a>
    <a href="#">Products</a>
    <a href="#">Features</a>
    <a href="#">Blog</a>
    <a href="#">Pricing</a>
    <a href="#">Contact us</a>
  </nav>
  <div class="header-tools">
    <a class="search-btn" href="#" aria-label="Search">
      <svg width="13" height="13" viewBox="0 0 13 13"><circle cx="5.5" cy="5.5" r="4" fill="none" stroke="#2a2a2a" stroke-width="2"/><line x1="8.5" y1="8.5" x2="12" y2="12" stroke="#2a2a2a" stroke-width="2"/></svg>
    </a>
    <a class="round-btn lock" href="#" aria-label="Log in">
      <svg width="14" height="16" viewBox="0 0 14 16"><path d="M3.5 7V5a3.5 3.5 0 0 1 7 0v2" fill="none" stroke="#fff" stroke-width="2"/><rect x="1" y="7" width="12" height="9" rx="1.5" fill="#fff"/></svg>
    </a>
    <a class="round-btn edit" href="#" aria-label="Sign up">
      <svg width="16" height="16" viewBox="0 0 16 16"><path d="M2 14l1-4 8-8 3 3-8 8z" fill="#fff"/></svg>
    </a>
  </div>
</header>

<section class="hero">
  <div class="hero-visual" role="img" aria-label="Hand holding a tablet with colourful app icons bursting out of the screen"></div>
  <div class="hero-panel">
    <h1 class="hero-title">KOLVARIN</h1>
    <p class="hero-lead">We provide creative design, app creation,<br>new product innovation etc</p>
    <a class="btn" href="#">Get started</a>
  </div>
  <div class="slider-dots"><span class="is-on"></span><span></span><span></span><span></span></div>
</section>

<section class="welcome">
  <h2 class="section-title">Welcome to Kolvarin</h2>
  <p class="welcome-intro">At vero eos et accusamus et iusto odio dignissimos ducimus qui blanditiis praesentium voluptatum deleniti atque corrupti quos dolores et quas molestias excepturi sint occaecati cupiditate non prova qui officia deserunt mollitia arum et dolorum fuga</p>
  <div class="services">
    <article class="service service--design">
      <div class="service-icon"><div class="disc">
        <svg width="64" height="46" viewBox="0 0 64 46"><rect x="9" y="3" width="46" height="31" rx="2" fill="none" stroke="#fff" stroke-width="3"/><path d="M2 38h60l-4 5H6z" fill="#fff"/><path d="M26 27l14-16" stroke="#fff" stroke-width="3" stroke-linecap="round"/></svg>
      </div></div>
      <h3>Creative design</h3>
      <p>Lam libero tempore, cum soluta nobis est eligendi<br>optio cumque nihil impedit quo minus</p>
      <a class="read-more" href="#">Read more &gt;&gt;</a>
    </article>
    <article class="service service--app">
      <div class="service-icon"><div class="disc">
        <svg width="64" height="46" viewBox="0 0 64 46"><rect x="9" y="3" width="46" height="31" rx="2" fill="none" stroke="#fff" stroke-width="3"/><path d="M2 38h60l-4 5H6z" fill="#fff"/><path d="M26 13l-6 6 6 6M38 13l6 6-6 6M34 11l-4 16" fill="none" stroke="#fff" stroke-width="2.5" stroke-linecap="round"/></svg>
      </div></div>
      <h3>App creation</h3>
      <p>Lam libero tempore, cum soluta nobis est eligendi<br>optio cumque nihil impedit quo minus</p>
      <a class="read-more" href="#">Read more &gt;&gt;</a>
    </article>
    <article class="service service--idea">
      <div class="service-icon"><div class="disc">
        <svg width="56" height="56" viewBox="0 0 56 56"><circle cx="28" cy="28" r="24" fill="none" stroke="#fff" stroke-width="3" stroke-dasharray="30 8"/><path d="M28 14a9 9 0 0 0-5 16.5V35h10v-4.5A9 9 0 0 0 28 14z" fill="none" stroke="#fff" stroke-width="2.5"/><line x1="23" y1="39" x2="33" y2="39" stroke="#fff" stroke-width="2.5"/></svg>
      </div></div>
      <h3>New product innovation</h3>
      <p>Lam libero tempore, cum soluta nobis est eligendi<br>optio cumque nihil impedit quo minus</p>
      <a class="read-more" href="#">Read more &gt;&gt;</a>
    </article>
  </div>
</section>

<section class="cta-band">
  <div class="cta-visual" role="img" aria-label="Dark photo of hands holding a phone with faint floating icons"></div>
  <div class="cta-content">
    <h2 class="section-title">Get started</h2>
    <p>On the other hand, we denounce with righteous indignation and dislike men who are so beguiled and demoralized by the charms of pleasure of the moment, so blinded by desire,</p>
    <a class="btn" href="#">Get started</a>
  </div>
</section>

<section class="features">
  <div class="devices-visual" role="img" aria-label="Desktop monitor and smartphone showing a grid of colourful fruit app tiles"></div>
  <div class="features-copy">
    <h2 class="section-title">Key features</h2>
    <ul class="feature-list">
      <li><svg class="tick" viewBox="0 0 13 13"><circle cx="6.5" cy="6.5" r="6.5" fill="#4fa846"/><path d="M3.5 6.7l2 2 4-4" fill="none" stroke="#fff" stroke-width="1.8"/></svg>On the other hand, we denounce with righteous indignation and dislike.</li>
      <li><svg class="tick" viewBox="0 0 13 13"><circle cx="6.5" cy="6.5" r="6.5" fill="#4fa846"/><path d="M3.5 6.7l2 2 4-4" fill="none" stroke="#fff" stroke-width="1.8"/></svg>At vero eos et accusamus et iusto odio dignissimos ducimus qui blanditiis.</li>
      <li><svg class="tick" viewBox="0 0 13 13"><circle cx="6.5" cy="6.5" r="6.5" fill="#4fa846"/><path d="M3.5 6.7l2 2 4-4" fill="none" stroke="#fff" stroke-width="1.8"/></svg>Certain circumstances and owing to the claims of duty or the oblig</li>
      <li><svg class="tick" viewBox="0 0 13 13"><circle cx="6.5" cy="6.5" r="6.5" fill="#4fa846"/><path d="M3.5 6.7l2 2 4-4" fill="none" stroke="#fff" stroke-width="1.8"/></svg>On the other hand, we denounce with righteous indignation and dislike.</li>
      <li><svg class="tick" viewBox="0 0 13 13"><circle cx="6.5" cy="6.5" r="6.5" fill="#4fa846"/><path d="M3.5 6.7l2 2 4-4" fill="none" stroke="#fff" stroke-width="1.8"/></svg>Nemo enim ipsam voluptatem quia voluptas sit aspernatur aut odit aut fugit,</li>
    </ul>
    <a class="read-more" href="#">Read more &gt;&gt;</a>
  </div>
</section>

<section class="testimonials">
  <div class="testimonials-visual" role="img" aria-label="Green tinted background of many small portrait photos"></div>
  <h2 class="section-title">Testimonials</h2>
  <div class="quote-badge">
    <svg width="40" height="30" viewBox="0 0 40 30"><path d="M2 30V17C2 8 7 2 16 0v6c-5 2-7 5-7 9h7v15zM24 30V17c0-9 5-15 14-17v6c-5 2-7 5-7 9h7v15z" fill="#c9c9c9"/></svg>
  </div>
  <div class="avatar" role="img" aria-label="Portrait photo of the client giving the testimonial"></div>
  <p class="testimonial-text">It is a long established fact that a reader will be distracted by the readable content of a page when looking at its layout. The point of using Lorem Ipsum is that it has a more-or-less normal distribution of letters, as opposed to using 'Content here, content here', making it look like readable English.</p>
  <p class="testimonial-name">Dara Velmont</p>
  <div class="slider-dots"><span class="is-on"></span><span></span><span></span></div>
</section>

<section class="partners">
  <h2 class="section-title">Our partners</h2>
  <svg class="carousel-arrow prev" viewBox="0 0 16 28"><path d="M13 3L4 14l9 11" fill="none" stroke="#9a9a9a" stroke-width="2.5"/></svg>
  <div class="partner-row">
    <div class="partner" aria-label="Partner"><span class="partner-badge" style="background:#1f6fb2"></span></div>
    <div class="partner" aria-label="Partner"><span class="partner-badge" style="background:#8fb4d4"></span></div>
    <div class="partner" aria-label="Partner"><span class="partner-badge" style="background:#3a3f57"></span></div>
    <div class="partner" aria-label="Partner"><span class="partner-badge" style="background:#4a78b0"></span></div>
    <div class="partner" aria-label="Partner"><span class="partner-badge" style="background:#9bbf3a"></span></div>
  </div>
  <svg class="carousel-arrow next" viewBox="0 0 16 28"><path d="M3 3l9 11-9 11" fill="none" stroke="#9a9a9a" stroke-width="2.5"/></svg>
</section>

<footer class="site-footer">
  <div class="rainbow"></div>
  <div class="footer-brand">
    <span class="brand-mark"></span>
    <span class="brand-name">KOLVARIN</span>
  </div>
  <div class="footer-cols">
    <div class="footer-col">
      <h4>About us</h4>
      <ul><li>Our Story</li><li>Team</li><li>Newsletters</li><li>Contact</li><li>Jobs</li><li>Help Us Grow</li></ul>
    </div>
    <div class="footer-col">
      <h4>Products</h4>
      <ul><li>Crewline Projects</li><li>Crewline Desk</li><li>Crewline Chat</li></ul>
    </div>
    <div class="footer-col">
      <h4>Links</h4>
      <ul><li>Desktop Timer App</li><li>Suite Apps for Business</li><li>Tablet App</li><li>Handset App</li><li>Droidix App</li></ul>
    </div>
    <div class="footer-col">
      <h4>Resources</h4>
      <ul><li>Roadmap &amp; Updates</li><li>Security</li><li>Privacy Policy</li><li>Terms of Service</li><li>Webinars</li><li>Free for Startups</li></ul>
    </div>
    <div class="footer-col">
      <h4>Legal</h4>
      <ul><li>Certified Trainers</li><li>Crewline</li><li>Developer Zone</li><li>Referral Program</li><li>Refund Policy</li><li>Login</li></ul>
    </div>
  </div>
  <p class="copyright">Copyrights © 2016, Kolvarin. All rights reserved.</p>
  <div class="social">
    <a class="mirtavel" href="#">mirtavel</a>
    <a class="plimber" href="#">plimber</a>
    <a class="trelvanet" href="#">trelvanet</a>
    <a class="vendoloop" href="#">vendoloop</a>
  </div>
</footer>

</body>
</html>
```